Create Premium Wine Label Design

We are premium wine exporters from Australia. We are looking to introduce new brand " The Velmora" - in red wine, White wine and Sparkling wine to international market.

The sample label design for red wine ( Shiraz) is attached.

This is our luxury brand. We need a stunning wine label designs for (front, back and neck) that should be mostly in GOLD colour and design should be really eye catching.

We have provided sample design for front, back and neck labels. However, we are looking forward to see a completely new improvised design.

LOGO attached.

Front Label Design Specification:

* We would like to see designs that are in Gold colour.
* Wine Bottle size is standard: 750ml; we assume the same design can be resizable to different bottle sizes.
* Our design should suit both black, white and sparkling wine bottles(sample attached)
* Use our logo in the design (see attached - label sample)
* Content for front label (see attached).
* Design should include all information specified in the sample

Back Label Design
* All contents in the sample should be used ( sample attached)
* LOGO attached.

Neck Label Design
* Sample of Neck label attached, please provide similar or your own design.
* LOGO attached.

Image Samples:
* Samples of label designs we like (see attached)
* Sample for gold color (see attached)
* For bottle shapes (see attached)
* Front, Back and Neck Label Samples (see attached)

Target Market(s)

International Wine Market

Font styles to use
Decorative
Script

Requirements
Must have
• Must have golden color on front and back label

```html
<!DOCTYPE html>
<html lang="en">
<head>
<meta charset="utf-8">
<title>The Velmora Shiraz 2018 – Front Label</title>
<link href="https://fonts.googleapis.com/css2?family=Cinzel+Decorative:wght@700&family=Cinzel:wght@700&family=Playfair+Display:wght@900&display=swap" rel="stylesheet">
<style>
  :root {
    --page: #ffffff;
    --label-black: #000000;
    --gold-mid: #d4a52a;
    --gold-sheen: linear-gradient(135deg, #b8862a 0%, #f6e27a 25%, #d9ac3a 45%, #fff1a8 60%, #c0902c 80%, #e9c75a 100%);
    --year-white: #ffffff;
    --band-ink: #111111;
  }
  * { box-sizing: border-box; margin: 0; padding: 0; }
  html, body {
    width: 1200px; height: 1200px; overflow: hidden;
    background: var(--page);
  }
  .canvas { position: relative; width: 1200px; height: 1200px; }

  .front-label {
    position: absolute; left: 229px; top: 80px;
    width: 742px; height: 1052px;
    background: var(--label-black);
    overflow: hidden;
  }

  .gold-text {
    background: var(--gold-sheen);
    -webkit-background-clip: text; background-clip: text;
    color: transparent;
  }

  .brand-mark {
    position: absolute; top: 48px; left: 326px;
    width: 90px; height: 90px; border-radius: 50%;
    background: var(--gold-mid);
  }
  .brand-name {
    position: absolute; top: 160px; left: 0; width: 100%;
    text-align: center;
    font-family: "Cinzel", serif; font-weight: 700;
    font-size: 52px; line-height: 1; letter-spacing: 1px;
    color: var(--gold-mid);
  }

  .floral-field {
    position: absolute; left: 35px; top: 272px;
    width: 672px; height: 680px; border-radius: 50%;
    background: radial-gradient(circle, #2e2e2e 0%, #262626 55%, #141414 85%, rgba(0,0,0,0) 100%);
  }

  .varietal {
    position: absolute; top: 458px; left: 0; width: 100%;
    text-align: center;
    font-family: "Playfair Display", serif; font-weight: 900;
    font-size: 84px; letter-spacing: 16px; line-height: 1;
    padding-left: 16px;
  }

  .wine-name {
    position: absolute; top: 560px; left: 0; width: 100%;
    display: flex; justify-content: center; align-items: center;
    gap: 6px;
  }
  .wine-name-article {
    font-family: "Playfair Display", serif; font-weight: 900;
    font-size: 26px; line-height: 1; letter-spacing: 2px;
    writing-mode: vertical-rl;
    transform: rotate(180deg);
  }
  .wine-name-main {
    font-family: "Playfair Display", serif; font-weight: 900;
    font-size: 110px; line-height: 1.1; letter-spacing: 1px;
  }

  .vintage {
    position: absolute; top: 728px; left: 0; width: 100%;
    text-align: center;
    font-family: "Playfair Display", serif; font-weight: 900;
    font-variant-numeric: lining-nums;
    font-size: 84px; line-height: 1;
    color: var(--year-white);
  }

  .origin-band {
    position: absolute; left: 0; top: 970px;
    width: 100%; height: 62px;
    background: linear-gradient(90deg, #c99a2e 0%, #f4dc72 20%, #d8ad40 45%, #f8e68a 65%, #c4922a 85%, #e7c45a 100%);
    display: flex; align-items: center; justify-content: center;
  }
  .origin-text {
    font-family: "Cinzel Decorative", serif; font-weight: 700;
    font-size: 40px; line-height: 1; color: var(--band-ink); letter-spacing: 0.5px;
  }
</style>
</head>
<body>
<main class="canvas">
  <section class="front-label">
    <span class="brand-mark" aria-hidden="true"></span>
    <p class="brand-name">Ambervale</p>

    <div class="floral-field" role="img" aria-label="Grey line-art floral mandala pattern of interlocking flowers and leaves"></div>

    <h1 class="varietal gold-text">SHIRAZ</h1>

    <h2 class="wine-name">
      <span class="wine-name-article gold-text">THE</span>
      <span class="wine-name-main gold-text">VELMORA</span>
    </h2>

    <p class="vintage">2018</p>

    <div class="origin-band">
      <p class="origin-text">Wine of Australia</p>
    </div>
  </section>
</main>
</body>
</html>
```